Law Offices business card

Hi there, I'll need business card for the Law Offices of Colin Matheny. The information must convey his strategic approach and quick resolution to complex business litigation needs. Please emphasize Civil Litigation, Corporate Law, Business Governance and Real Estate Law. Colin has over 25 years of experience in these fields.The card should be modern and edgy and the message should be clear. Please consult his current website for ideas.

```html
<!DOCTYPE html>
<html lang="en">
<head>
<meta charset="utf-8">
<title>Law Offices of Colin Matheny – Business Card</title>
<link rel="stylesheet" href="https://fonts.googleapis.com/css2?family=Lato:wght@400;700&display=swap">
<style>
  :root {
    --backdrop: #9b9b9b;
    --card-black: #050505;
    --brand-red: #a33d3f;
    --accent-red: #b8393d;
    --line-red: #8e1f24;
    --paper-white: #eeeeee;
    --text-white: #f2f2f2;
    --logo-grey: #e6e2e2;
  }
  html, body {
    margin: 0;
    padding: 0;
    width: 1105px;
    height: 1200px;
    overflow: hidden;
    background: var(--backdrop);
    font-family: "Lato", Arial, sans-serif;
  }
  .canvas {
    position: relative;
    width: 1105px;
    height: 1200px;
  }
  .card {
    position: absolute;
    left: 180px;
    width: 746px;
    height: 427px;
    overflow: hidden;
  }
  .card--front { top: 119px; background: var(--card-black); }
  .card--back  { top: 637px; background: var(--brand-red); }

  /* front */
  .firm-name {
    position: absolute;
    display: flex;
    align-items: center;
    gap: 10px;
    color: var(--text-white);
    font-weight: 400;
    line-height: 1.05;
  }
  .firm-name__mark {
    width: 14px;
    height: 14px;
    background: var(--accent-red);
    flex: none;
  }
  .card--front .firm-name {
    left: 46px;
    top: 48px;
    font-size: 27px;
  }
  .person-name {
    position: absolute;
    left: 47px;
    top: 149px;
    margin: 0;
    color: var(--accent-red);
    font-size: 22px;
    font-weight: 400;
    letter-spacing: 0.5px;
  }
  .person-title {
    position: absolute;
    left: 47px;
    top: 182px;
    margin: 0;
    color: var(--text-white);
    font-size: 17px;
    letter-spacing: 0.6px;
  }
  .address {
    position: absolute;
    left: 47px;
    top: 220px;
    margin: 0;
    color: var(--text-white);
    font-style: normal;
    font-size: 18px;
    line-height: 25px;
  }
  .contacts {
    position: absolute;
    left: 47px;
    top: 280px;
    margin: 0;
    padding: 0;
    list-style: none;
    color: var(--text-white);
    font-size: 18px;
  }
  .contacts li {
    display: flex;
    align-items: center;
    height: 28.5px;
  }
  .contacts svg {
    width: 17px;
    height: 17px;
    margin-right: 14px;
    fill: var(--accent-red);
  }
  .edge-line {
    position: absolute;
    left: 644px;
    top: 0;
    width: 12px;
    height: 100%;
    background: var(--line-red);
  }
  .edge-band {
    position: absolute;
    left: 656px;
    top: 0;
    width: 90px;
    height: 100%;
    background: var(--paper-white);
  }

  /* back */
  .card--back .firm-name {
    left: 0;
    right: 0;
    top: 170px;
    justify-content: center;
    color: var(--logo-grey);
    font-size: 36px;
  }
  .card--back .firm-name__mark { background: var(--logo-grey); width: 18px; height: 18px; }
</style>
</head>
<body>
<main class="canvas">
  <section class="card card--front" aria-label="Business card front">
    <div class="firm-name">
      <span class="firm-name__mark"></span>
      <span>Law Offices of<br>Colin Matheny, PA</span>
    </div>
    <h1 class="person-name">COLIN MATHENY</h1>
    <p class="person-title">ATTORNEY</p>
    <address class="address">318B Harbor Lane<br>Coral Bay, Florida 33921</address>
    <ul class="contacts">
      <li>
        <svg viewBox="0 0 24 24" aria-hidden="true"><path d="M6.6 10.8a15.1 15.1 0 0 0 6.6 6.6l2.2-2.2a1 1 0 0 1 1-.25 11.4 11.4 0 0 0 3.6.57 1 1 0 0 1 1 1V20a1 1 0 0 1-1 1A17 17 0 0 1 3 4a1 1 0 0 1 1-1h3.5a1 1 0 0 1 1 1c0 1.25.2 2.45.57 3.57a1 1 0 0 1-.25 1z"/></svg>
        561-555-0142
      </li>
      <li>
        <svg viewBox="0 0 24 24" aria-hidden="true"><path d="M7 2h10v5H7z M3 9h18a1 1 0 0 1 1 1v8h-4v4H6v-4H2v-8a1 1 0 0 1 1-1z M8 15v5h8v-5z"/></svg>
        561-555-0187
      </li>
      <li>
        <svg viewBox="0 0 24 24" aria-hidden="true"><path d="M2 5h20v2l-10 6L2 7z M2 9.3l10 6 10-6V19H2z"/></svg>
        colin@mathenylaw.com
      </li>
      <li>
        <svg viewBox="0 0 24 24" aria-hidden="true"><path d="M12 2a10 10 0 1 0 0 20 10 10 0 0 0 0-20zm-1 17.9A8 8 0 0 1 4.2 10.2L9 15v1a2 2 0 0 0 2 2zm6.9-2.5A2 2 0 0 0 16 16h-1v-3a1 1 0 0 0-1-1H8v-2h2a1 1 0 0 0 1-1V7h2a2 2 0 0 0 2-2v-.4a8 8 0 0 1 2.9 12.8z"/></svg>
        www.mathenylaw.com
      </li>
    </ul>
    <div class="edge-line"></div>
    <div class="edge-band"></div>
  </section>

  <section class="card card--back" aria-label="Business card back">
    <div class="firm-name">
      <span class="firm-name__mark"></span>
      <span>Law Offices of<br>Colin Matheny, PA</span>
    </div>
  </section>
</main>
</body>
</html>
```